Logo & Visitenkarte für Helga Tormann Interim Management
Sehr schöne Umsetzung meiner Vorstellungen, super Arbeit, problemlose und unkomplizierte Abwicklung. Kann ich sehr empfehlen!
Zielgruppe
Interim Management mit Schwerpunkt Einkauf
Zielgruppen sind sowohl Endkunden als auch Agenturen
Aufgabenstellung
Logo/Slogan sollen erkennen lassen, worum es sich handelt, damit auch die richtigen Zielgruppen angesprochen werden und ersichtlich ist, was angeboten wird.
Das Logo/Slogan soll zwar seriös wirken, aber auf keinen Fall langweilig!
Farbe wäre schön.
Bezug zu meinem Namen (Initialen ins Logo integrieren).
Ob nur Logo oder in Verbindung mit einem Slogan überlasse ich der Kreativität der Designer.

```html
<!DOCTYPE html>
<html lang="de">
<head>
<meta charset="utf-8">
<title>Helga Tormann Interim Management – Logo &amp; Visitenkarten</title>
<link href="https://fonts.googleapis.com/css2?family=Michroma&family=Montserrat:wght@400;600&display=swap" rel="stylesheet">
<style>
  :root {
    --pink: #e5176f;
    --magenta: #b3146f;
    --grey: #6d6d6d;
    --ink: #111111;
    --paper: #ffffff;
    --text: #555555;
  }
  * { box-sizing: border-box; margin: 0; padding: 0; }
  html, body { width: 1200px; height: 1168px; overflow: hidden; background: var(--paper); }
  body { position: relative; font-family: "Montserrat", sans-serif; color: var(--text); }

  .brand { position: absolute; text-align: center; color: var(--pink); font-family: "Michroma", sans-serif; }
  .brand .square { display: block; margin: 0 auto; background: var(--grey); }
  .brand .name { display: block; white-space: nowrap; }
  .brand .tag { display: block; white-space: nowrap; }

  .primary { left: 90px; width: 400px; }
  .primary .square { width: 46px; height: 46px; margin-bottom: 28px; }
  .primary .name { font-size: 22px; letter-spacing: 2px; line-height: 1.1; }
  .primary .tag { font-size: 11px; letter-spacing: 3.5px; margin-top: 6px; }

  .card { position: absolute; width: 236px; height: 152px; overflow: hidden; }
  .card.front { left: 506px; background: var(--ink); }
  .card.back { left: 794px; background: var(--paper); box-shadow: 0 1px 4px rgba(0,0,0,.25); }

  .card .brand.center { left: 0; right: 0; top: 42px; }
  .card .brand .square { width: 30px; height: 30px; margin-bottom: 14px; }
  .card .brand .name { font-size: 12.5px; letter-spacing: 1px; }
  .card .brand .tag { font-size: 6px; letter-spacing: 1.6px; margin-top: 3px; }

  .stripe { position: absolute; left: 0; right: 0; height: 4px; background: var(--pink); }
  .stripe.top { top: 0; }
  .stripe.bottom { bottom: 0; }

  .brand.inline { display: flex; align-items: center; gap: 10px; text-align: left; }
  .brand.inline .square { width: 24px; height: 24px; margin: 0; }
  .brand.inline .name { font-size: 11px; }
  .brand.inline .tag { font-size: 5.5px; margin-top: 2px; }

  .contact { position: absolute; font-size: 7.5px; line-height: 1.35; color: var(--text); font-family: "Michroma", sans-serif; }
  .contact .row { display: flex; align-items: center; gap: 5px; }
  .contact .gap { height: 6px; }
  .icon { width: 7px; height: 7px; flex: none; }

  .band { position: absolute; left: 0; right: 0; background: var(--magenta); color: #fff; font-size: 7px; line-height: 1.3; }
  .band .left { position: absolute; left: 18px; top: 26px; }
  .band .right { position: absolute; left: 125px; top: 16px; }
  .band .row { display: flex; align-items: center; gap: 5px; }

  .rule { position: absolute; background: var(--pink); }
  .person { font-family: "Montserrat", sans-serif; font-size: 7.5px; color: #444; }
  .person strong { font-weight: 600; }
</style>
</head>
<body>

<svg width="0" height="0" style="position:absolute" aria-hidden="true">
  <symbol id="i-phone" viewBox="0 0 10 10"><rect x="2.5" y="0.5" width="5" height="9" rx="1" fill="none" stroke="currentColor"/><line x1="4" y1="8" x2="6" y2="8" stroke="currentColor"/></symbol>
  <symbol id="i-at" viewBox="0 0 10 10"><circle cx="5" cy="5" r="4.2" fill="none" stroke="currentColor" stroke-width="1.2"/><circle cx="5" cy="5" r="1.8" fill="none" stroke="currentColor" stroke-width="1.2"/></symbol>
  <symbol id="i-web" viewBox="0 0 10 10"><circle cx="5" cy="5" r="4.2" fill="none" stroke="currentColor"/><ellipse cx="5" cy="5" rx="1.8" ry="4.2" fill="none" stroke="currentColor"/><line x1="0.8" y1="5" x2="9.2" y2="5" stroke="currentColor"/></symbol>
</svg>

<!-- Row 1 -->
<div class="brand primary" style="top:185px">
  <span class="square"></span><span class="name">HELGA TORMANN</span><span class="tag">INTERIM MANAGEMENT</span>
</div>
<div class="card front" style="top:148px">
  <div class="stripe top"></div>
  <div class="brand center"><span class="square"></span><span class="name">HELGA TORMANN</span><span class="tag">INTERIM MANAGEMENT</span></div>
</div>
<div class="card back" style="top:148px">
  <div class="stripe top"></div>
  <div class="brand inline" style="left:20px;top:26px"><span class="square"></span><div><span class="name">HELGA TORMANN</span><span class="tag">INTERIM MANAGEMENT</span></div></div>
  <div class="contact" style="left:72px;top:84px">
    <div>Musterstraße 123</div><div>12345 Musterhausen</div><div class="gap"></div>
    <div class="row"><svg class="icon"><use href="#i-phone"/></svg>+49 (0) 123 123 123</div>
    <div class="row"><svg class="icon"><use href="#i-at"/></svg>info@helgatormann.de</div>
    <div class="row"><svg class="icon"><use href="#i-web"/></svg>www.helgatormann.de</div>
  </div>
</div>

<!-- Row 2 -->
<div class="brand primary" style="top:422px">
  <span class="square"></span><span class="name">HELGA TORMANN</span><span class="tag">INTERIM MANAGEMENT</span>
</div>
<div class="card front" style="top:396px">
  <div class="brand center"><span class="square"></span><span class="name">HELGA TORMANN</span><span class="tag">INTERIM MANAGEMENT</span></div>
</div>
<div class="card back" style="top:396px">
  <div class="stripe top" style="background:var(--magenta);height:4px"></div>
  <div class="stripe top" style="background:var(--ink);height:1.5px;top:6px"></div>
  <div class="brand center" style="top:22px"><span class="square"></span><span class="name">HELGA TORMANN</span><span class="tag">INTERIM MANAGEMENT</span></div>
  <div class="band" style="top:96px;height:52px">
    <div class="left">Helga Tormann<br>Musterstraße 123<br>12345 Musterhausen</div>
    <div class="right">
      <div class="row"><svg class="icon"><use href="#i-phone"/></svg>+49 (0) 123 123 123</div>
      <div class="row"><svg class="icon"><use href="#i-at"/></svg>info@helgatormann.de</div>
      <div class="row"><svg class="icon"><use href="#i-web"/></svg>www.helgatormann.de</div>
    </div>
  </div>
  <div class="stripe bottom" style="background:var(--ink);height:3px"></div>
</div>

<!-- Row 3 -->
<div class="brand primary" style="top:665px">
  <span class="square"></span><span class="name">HELGA TORMANN</span><span class="tag">INTERIM MANAGEMENT</span>
</div>
<div class="card front" style="top:634px">
  <div class="brand center"><span class="square"></span><span class="name">HELGA TORMANN</span><span class="tag">INTERIM MANAGEMENT</span></div>
</div>
<div class="card back" style="top:634px">
  <div class="brand" style="left:14px;top:40px;width:80px"><span class="square" style="width:40px;height:40px"></span></div>
  <div class="rule" style="left:100px;top:40px;width:1.5px;height:88px"></div>
  <div class="contact person" style="left:118px;top:38px">
    <div><strong>Helga Tormann</strong></div><div><strong>Interim Management</strong></div><div class="gap"></div>
    <div>Musterstraße 123</div><div>12345 Musterhausen</div><div class="gap"></div>
    <div class="row"><svg class="icon"><use href="#i-phone"/></svg>+49 (0) 123 123 123</div>
    <div class="row"><svg class="icon"><use href="#i-at"/></svg>info@helgatormann.de</div>
    <div class="row"><svg class="icon"><use href="#i-web"/></svg>www.helgatormann.de</div>
  </div>
</div>

<!-- Row 4 -->
<div class="brand primary" style="top:902px">
  <span class="square"></span><span class="name">HELGA TORMANN</span><span class="tag">INTERIM MANAGEMENT</span>
</div>
<div class="card front" style="top:869px">
  <div class="brand center"><span class="square"></span><span class="name">HELGA TORMANN</span><span class="tag">INTERIM MANAGEMENT</span></div>
</div>
<div class="card back" style="top:869px">
  <div class="stripe top" style="background:var(--grey);right:50%"></div>
  <div class="stripe top" style="left:calc(50% + 2px)"></div>
  <div class="brand inline" style="left:26px;top:24px"><span class="square"></span><div><span class="name">HELGA TORMANN</span><span class="tag">INTERIM MANAGEMENT</span></div></div>
  <div class="contact" style="left:32px;top:74px">
    <div>Musterstraße 123</div><div>12345 Musterhausen</div><div class="gap"></div>
    <div class="row"><svg class="icon"><use href="#i-phone"/></svg>+49 (0) 123 123 123</div>
    <div class="row"><svg class="icon"><use href="#i-at"/></svg>info@helgatormann.de</div>
    <div class="row"><svg class="icon"><use href="#i-web"/></svg>www.helgatormann.de</div>
  </div>
  <div class="stripe bottom" style="right:calc(50% + 2px)"></div>
  <div class="stripe bottom" style="background:var(--grey);left:50%"></div>
</div>

</body>
</html>
```